TK Homes - Stone Dorf Design

Looking for a double sides design, 1 side for my realestate and the other for home building. ( TK Homes on 1 side, Stone Dorf card on the other Side
Side 1 - Marek Tove ~ Vox Realty logo and Company ( the Property quarter )
Marek Tove
Marek@Marektove.example
IG - Marek_Bzq_Realtor
FB - marekt
Cell - 5558130467
3847 61 St Nw

Side 2
Marek Tove
5558130467
IG - Stonedorf_Bzq
Stonedorfdev@mailbox.example

Target Market(s)

Home buyers/ sellers

Industry/Entity Type

Home builders - Realestate

Contact Information for Business Card

Above

Requirements
Must have
• Black OR White background - my information -

```html
<!DOCTYPE html>
<html lang="en">
<head>
<meta charset="utf-8">
<title>Marek Tove – Business Cards</title>
<link rel="stylesheet" href="https://fonts.googleapis.com/css2?family=Tinos:wght@400;700&display=swap">
<style>
  :root {
    --page: #e4e5e8;
    --card: #f6f6f6;
    --card-white: #ffffff;
    --blue: #1d6fc4;
    --red: #d8283a;
    --ink: #111111;
    --ghost: #e6e6e6;
    --serif: "Tinos", "Times New Roman", serif;
  }
  * { box-sizing: border-box; margin: 0; padding: 0; }
  html, body { width: 1200px; height: 780px; overflow: hidden; }
  body {
    background: var(--page);
    font-family: var(--serif);
    color: var(--ink);
    position: relative;
  }
  .card {
    position: absolute;
    top: 230px;
    width: 540px;
    height: 320px;
    background: var(--card);
    box-shadow: 0 6px 18px rgba(0,0,0,.18);
    overflow: hidden;
  }
  .card--realty { left: 40px; }
  .card--builder { left: 620px; background: var(--card-white); }

  .ghost-mark {
    position: absolute;
    background: var(--ghost);
    z-index: 0;
  }
  .card--realty .ghost-mark { left: 232px; top: 206px; width: 86px; height: 114px; }
  .card--builder .ghost-mark { left: 196px; top: 206px; width: 110px; height: 114px; }

  .accent-band {
    position: absolute;
    right: 0;
    top: 206px;
    width: 22px;
    height: 44px;
    background: var(--red);
  }
  .signature {
    position: absolute;
    right: 34px;
    top: 188px;
    text-align: right;
    z-index: 1;
  }
  .signature__name {
    font-weight: 700;
    font-size: 34px;
    line-height: 1;
    color: var(--blue);
  }
  .signature__name .surname { color: var(--red); }
  .signature__title {
    font-weight: 700;
    font-size: 17px;
    margin-top: 4px;
    margin-right: 8px;
  }

  .brand-name {
    position: absolute;
    left: 32px;
    top: 30px;
    font-size: 30px;
    font-weight: 700;
    color: var(--blue);
    letter-spacing: 1px;
  }
  .address {
    position: absolute;
    left: 34px;
    top: 78px;
    font-size: 15px;
  }
  .contact-list {
    position: absolute;
    left: 34px;
    list-style: none;
    font-size: 15px;
    line-height: 1.22;
    z-index: 1;
  }
  .card--realty .contact-list { top: 104px; }
  .card--builder .contact-list { top: 128px; }
  .contact-list li { display: flex; align-items: center; gap: 7px; }
  .contact-list svg { width: 12px; height: 12px; flex: none; }
  .dot { width: 11px; height: 11px; border-radius: 50%; background: var(--blue); flex: none; }
  .square { width: 11px; height: 11px; background: var(--blue); flex: none; }

  .partner-name {
    position: absolute;
    left: 34px;
    bottom: 30px;
    font-size: 20px;
    font-weight: 700;
    color: var(--ink);
    z-index: 1;
  }

  .builder-name {
    position: absolute;
    left: 32px;
    top: 34px;
    font-size: 32px;
    line-height: 1.15;
    font-weight: 700;
    color: var(--blue);
    letter-spacing: 1px;
  }
</style>
</head>
<body>

  <section class="card card--realty" aria-label="Real estate side">
    <div class="ghost-mark" aria-hidden="true"></div>
    <div class="brand-name">Marek Tove</div>
    <p class="address">3847 61 St Nw</p>
    <ul class="contact-list">
      <li><svg viewBox="0 0 24 24"><path fill="#1d6fc4" d="M6.6 10.8a15 15 0 0 0 6.6 6.6l2.2-2.2c.3-.3.7-.4 1-.2 1.1.4 2.3.6 3.6.6.6 0 1 .4 1 1V20c0 .6-.4 1-1 1A17 17 0 0 1 3 4c0-.6.4-1 1-1h3.5c.6 0 1 .4 1 1 0 1.3.2 2.5.6 3.6.1.3 0 .7-.2 1z"/></svg>5558130467</li>
      <li><span class="dot"></span>marekt</li>
      <li><span class="square"></span>Marek_Bzq_Realtor</li>
      <li><svg viewBox="0 0 24 24"><rect x="2" y="5" width="20" height="14" fill="#1d6fc4"/><path d="M2 5l10 8 10-8" fill="none" stroke="#fff" stroke-width="2"/></svg>Marek@Marektove.example</li>
      <li><svg viewBox="0 0 24 24"><circle cx="12" cy="12" r="10" fill="none" stroke="#1d6fc4" stroke-width="2"/><path d="M2 12h20M12 2c3 3 3 17 0 20M12 2c-3 3-3 17 0 20" fill="none" stroke="#1d6fc4" stroke-width="2"/></svg>www.marektove.example</li>
    </ul>
    <div class="partner-name">the Property quarter</div>
    <div class="signature">
      <div class="signature__name">Marek <span class="surname">Tove</span></div>
      <div class="signature__title">Director</div>
    </div>
    <div class="accent-band"></div>
  </section>

  <section class="card card--builder" aria-label="Home building side">
    <div class="ghost-mark" aria-hidden="true"></div>
    <div class="builder-name">Stone Dorf<br>Developments</div>
    <ul class="contact-list">
      <li><svg viewBox="0 0 24 24"><path fill="#1d6fc4" d="M6.6 10.8a15 15 0 0 0 6.6 6.6l2.2-2.2c.3-.3.7-.4 1-.2 1.1.4 2.3.6 3.6.6.6 0 1 .4 1 1V20c0 .6-.4 1-1 1A17 17 0 0 1 3 4c0-.6.4-1 1-1h3.5c.6 0 1 .4 1 1 0 1.3.2 2.5.6 3.6.1.3 0 .7-.2 1z"/></svg>5558130467</li>
      <li><span class="square"></span>Stonedorf_Bzq</li>
      <li><svg viewBox="0 0 24 24"><rect x="2" y="5" width="20" height="14" fill="#1d6fc4"/><path d="M2 5l10 8 10-8" fill="none" stroke="#fff" stroke-width="2"/></svg>Stonedorfdev@mailbox.example</li>
    </ul>
    <div class="signature">
      <div class="signature__name">Marek <span class="surname">Tove</span></div>
      <div class="signature__title">Director</div>
    </div>
    <div class="accent-band"></div>
  </section>

</body>
</html>
```